Post Card Design - Photo on front, details on back. Logo on both sides.

Back: See the photo of my old card. The back worked well, as it gave me lots of space to write on. The address details are still correct, but the logo has changed to Josephine Sans. Logo can be on one line or on two (if two, align it on the left).
Don't include the 'BEAUTIFUL WEDDING DRESSES...' bit.
I'd like to print this on thicker, slightly coarse paper, so don't go too small on detail.
Here are the Trelo paper details: Paper Stock: Natural Uncoated
Paper Thickness: Premium
Finish: None
Front of Card: I'd like to see options for both pictures:
I think the painted image would look best with a frame in a pale shade and the logo in the frame fairly subtle.
The actual dress photo I'd like to see cropped a bit like in my mock up. You'll need to have a look at how the logo would be best placed on this. You can place it anywhere, or add a banner.
See my website for my brand's look: mirelhoffkin.co.nz
Target Market(s)
Brides
Industry/Entity Type
Wedding Dresses
Contact Information for Business Card
Front: Photo and logo. Back: with details and lots of empty space. See attached photos for loose brief.
Other font styles liked:
- Josephine Sans
Requirements
Must have
- I hand-write the gown designs and price on the back of the card, so there needs to be plenty of empty space.
Nice to have
- As per brief.
Should not have
- It must look clean, romantic, modern. Timeless.

```html
<!DOCTYPE html>
<html lang="en">
<head>
<meta charset="utf-8">
<title>Mirel Hoffkin – Postcard</title>
<link href="https://fonts.googleapis.com/css2?family=Josefin+Sans:wght@300;400;600&display=swap" rel="stylesheet">
<style>
  :root {
    --stage: #d4d4d4;
    --paper: #ffffff;
    --ink: #111111;
    --gold: #e2c9a0;
    --painting-base: #ecd49a;
    --painting-bloom: #eab3a6;
    --photo-light: #f3e3c8;
    --photo-warm: #c9a57c;
    --ghost-light: #ffffff;
    --ghost-grey: #e4e4e4;
  }
  * { box-sizing: border-box; margin: 0; padding: 0; }
  html, body {
    width: 1200px; height: 1200px; overflow: hidden;
    background: var(--stage);
    font-family: "Josefin Sans", sans-serif;
    color: var(--ink);
  }
  .card {
    position: absolute; left: 272px; width: 656px; height: 438px;
    background: var(--paper); overflow: hidden;
  }
  .card--front { top: 129px; }
  .card--back { top: 633px; }

  /* Front */
  .front-name {
    position: absolute; left: 30px; top: 26px;
    font-size: 30px; font-weight: 400; letter-spacing: 4.5px; line-height: 1;
  }
  .corner { position: absolute; border-color: var(--gold); border-style: solid; border-width: 0; }
  .corner--top-right { left: 295px; top: 9px; width: 48px; height: 49px; border-top-width: 1.5px; border-right-width: 1.5px; }
  .corner--bottom-left { left: 18px; top: 351px; width: 49px; height: 49px; border-bottom-width: 1.5px; border-left-width: 1.5px; }
  .dress-photo {
    position: absolute; left: 355px; top: 8px; width: 292px; height: 422px;
    background: linear-gradient(100deg, var(--photo-warm) 0%, var(--photo-light) 35%, #e8d2b0 60%, var(--photo-light) 80%, #b99068 100%);
  }
  .painting-frame {
    position: absolute; left: 21px; top: 61px; width: 396px; height: 335px;
    background: var(--paper); padding: 8px;
  }
  .painting {
    width: 100%; height: 100%;
    background: radial-gradient(ellipse at 50% 55%, var(--painting-bloom) 0%, #efc3a2 40%, var(--painting-base) 75%);
  }

  /* Back */
  .ghost-photo {
    position: absolute; left: 330px; top: 0; width: 326px; height: 438px;
    background: linear-gradient(90deg, var(--ghost-light) 0%, var(--ghost-grey) 45%, #ececec 75%, #f2f2f2 100%);
    -webkit-mask-image: linear-gradient(180deg, #000 70%, transparent 100%);
            mask-image: linear-gradient(180deg, #000 70%, transparent 100%);
  }
  .brand-name {
    position: absolute; left: 38px; top: 357px;
    font-size: 38px; font-weight: 400; letter-spacing: 1.5px; line-height: 1;
    white-space: nowrap;
  }
  .divider { position: absolute; left: 389px; top: 357px; width: 1px; height: 42px; background: var(--ink); }
  .contact { position: absolute; left: 415px; top: 353px; list-style: none; }
  .contact li { display: flex; align-items: center; gap: 7px; height: 16px; font-size: 11.5px; letter-spacing: 0.3px; white-space: nowrap; }
  .contact li.contact-phone { font-size: 14.5px; font-weight: 600; height: 18px; }
  .contact svg { width: 9px; height: 9px; flex: none; }
</style>
</head>
<body>

<section class="card card--front" aria-label="Postcard front">
  <div class="dress-photo" role="img" aria-label="Photograph of a bride in an off-shoulder fitted gown standing in a sunlit colonnade"></div>
  <span class="corner corner--top-right"></span>
  <span class="corner corner--bottom-left"></span>
  <h1 class="front-name">MIREL HOFFKIN</h1>
  <div class="painting-frame">
    <div class="painting" role="img" aria-label="Vintage painted illustration of a couple embracing among pink and peach flowers"></div>
  </div>
</section>

<section class="card card--back" aria-label="Postcard back">
  <div class="ghost-photo" role="img" aria-label="Faded photograph of a bride in a fitted gown"></div>
  <h2 class="brand-name">MIREL HOFFKIN</h2>
  <span class="divider"></span>
  <ul class="contact">
    <li class="contact-phone">
      <svg viewBox="0 0 10 10" aria-hidden="true"><path d="M2 1 L3.6 1 L4.2 3 L3.2 3.8 Q4.2 5.8 6.2 6.8 L7 5.8 L9 6.4 L9 8 Q8.5 9 7.5 9 Q1 8.5 1 2.5 Q1 1.5 2 1 Z" fill="var(--ink)"/></svg>
      +64 9 555 0147
    </li>
    <li>
      <svg viewBox="0 0 10 10" aria-hidden="true"><rect x="0.5" y="2" width="9" height="6" fill="var(--ink)"/><path d="M0.8 2.3 L5 5.5 L9.2 2.3" stroke="#fff" stroke-width="0.8" fill="none"/></svg>
      MIREL@MIRELHOFFKIN.CO.NZ
    </li>
    <li>
      <svg viewBox="0 0 10 10" aria-hidden="true"><circle cx="5" cy="5" r="4.2" fill="none" stroke="var(--ink)" stroke-width="1.2"/><path d="M1 5 H9 M5 1 Q2.5 5 5 9 M5 1 Q7.5 5 5 9" stroke="var(--ink)" stroke-width="0.8" fill="none"/></svg>
      MIRELHOFFKIN.CO.NZ
    </li>
  </ul>
</section>

</body>
</html>
```